New and upgraded www.valdmorefunds.com content & design financial markets

We need an upgrade of our site. The current site is www.valdmorefunds.com
Navigation with full site map i.e. the user can select any page from any menu item.

The “Insights” (Insikter) page will remain as is except new design AND with far more possibilities to add thumbnails, picts, videos etc. The user will have to logon to be able to read the full story.

The “Produkter & Tjänster” (“How to invest” in current web) will contain about the same info as the current “How to invest” pages.

Some pages will contain one or more videos and or speaker supported “live” graphics which we will supply. The media content shall be easy to change.

The site will have two languages from start, English and Swedish. There will be more languages added within 1 year or slightly more.

All texts will be provided by us.

I’m attaching a PDF with suggested content for some of the new pages. However this is just content and absolutely no design. We need new design for the total of the site as well as for the graphics.

Expectation info:
These sites (Both major players in our business) can be used as inspiration:
https://www.tarvenholm.com/eu/en/
https://www.brightwellpartners.com/index.html

Below some opt-OUT and opt-IN graphic rules in connection with the Web supporting our business acumen and brand:

Opt-OUT:
- images similar to educational comic books - it signals an authoritarian approach where the customer is small (insubstantial).
- images that signal trading, cyber, mystery and fast-paced business. We are extremely long-term and invest in real companies
- avoid images containing coins, calculators and banknotes. We're not a savings bank company. or payment service-branch
- avoid images of large data flows, because we should not make facts complex, but simple and comprehensible
- avoid sensing pictures of photo models. We are real people who stand for our efforts. We're not going to hide.
- avoid pictures of suits and tie. They signal rigid-banking. We're smart-investment, flexible, adaptable. Rather curl up your sleeves and show that we’re building something valuable.
- avoid pictures of skyscrapers and cool bank pictures - because they signal the more old valuations of big capital and giant banks - that we are not at all. I know we've had clean facades before. As long as we're not talking about bank skyscrapers, I'm in.

Opt-IN
- pictures of Lukas in moderate amount - he is our symbol person
- films with Lukas and explaining graphical films - explaining and clarifying
- images of pedagogy that give the customer a sense of overview and insights that we give to the customers in our service
- illustrations that explain and deepen our work
- pictures and bars that in 3d illustrate our consistent results and stable delivery
- images that signal that we have a full grasp of data, flows and analyses - without the image becoming a space adventure
- use the logo as a grid, shape and colour.
- no genre portraits, rather pictures of real customers - which gives a sense of why they are customers here
- images that support our core i.e. is science, innovation, unrestricted thinking (“out of the box” – (don’t like that sentence)), smart-solutions, data-driven, client-cantered, flexible and adaptable to client needs and expectation.
- Solid - to be trustworthy in any economic climate
- Long term - consistent work and choices. No trading. Numbers talk
- Data-driven - real tech - combining years of work in finance with straight on tech

Presenting on the webpage:
The story in text and illustration
Show the truth - we have a great history to show and give space
Only numbers and graphs that has a meaning - no artificial numbers etc.
Updates

Target Market(s)

Europe

Coding

Coded - Design and coding required

Number of Pages Required

5+ page

Colors

Designer to choose colors to be used in the design.

Requirements
Must have
• Colours in line with www.valdmorefunds.com

```html
<!DOCTYPE html>
<html lang="en">
<head>
<meta charset="utf-8">
<title>Valdmore Funds – Your Personal Investment Advisor</title>
<link href="https://fonts.googleapis.com/css2?family=Libre+Franklin:wght@300;400;500;600;700&display=swap" rel="stylesheet">
<style>
:root{
  --navy:#0b1a4b;
  --navy-deep:#07122f;
  --blue:#1b3aa5;
  --blue-bright:#2a4fd0;
  --ink:#1e2233;
  --text:#4a4f63;
  --light:#f1f2f8;
  --white:#ffffff;
  --line:#d7dae6;
}
*{box-sizing:border-box;margin:0;padding:0}
html,body{width:1200px;height:5186px;overflow:hidden}
body{font-family:"Libre Franklin",Arial,sans-serif;color:var(--text);background:var(--white);position:relative}
.abs{position:absolute}
.btn{display:inline-block;background:var(--blue);color:var(--white);font-weight:600;text-transform:uppercase;text-decoration:none;box-shadow:0 3px 8px rgba(11,26,75,.35)}
.brand{display:flex;align-items:center;gap:12px;color:var(--navy);font-weight:400;text-decoration:none}
.brand-mark{width:28px;height:28px;background:var(--navy)}

/* header */
.site-header{top:0;left:0;width:1200px;height:85px;background:var(--white);z-index:5}
.site-header .brand{position:absolute;left:48px;top:22px;font-size:38px}
.main-nav{position:absolute;left:404px;top:34px;display:flex;gap:27px;font-size:14px;font-weight:600;color:var(--ink);text-transform:uppercase}
.main-nav .active{color:var(--blue)}
.login{position:absolute;left:1049px;top:25px;width:108px;height:38px;line-height:38px;text-align:center;font-size:14px;border-radius:2px}

/* hero */
.hero{top:85px;left:0;width:1200px;height:665px;background:linear-gradient(100deg,#08112a 0%,#0c1c45 55%,#0f2a6b 100%);overflow:hidden}
.hero-visual{position:absolute;left:300px;top:40px;width:900px;height:540px;background:radial-gradient(ellipse at 70% 45%,rgba(42,90,230,.55),rgba(10,30,80,0) 65%)}
.hero-copy{position:absolute;left:145px;top:138px;color:var(--white)}
.hero-copy h1{font-size:40px;line-height:49px;font-weight:700;letter-spacing:.5px}
.hero-copy p{margin-top:16px;font-size:24px;line-height:32px;font-weight:400}
.hero-copy .btn{margin-top:22px;width:157px;height:40px;line-height:40px;text-align:center;font-size:16px;box-shadow:none}
.dots{display:flex;gap:9px;margin-top:18px}
.dots span{width:17px;height:17px;border:2px solid var(--white);border-radius:50%}
.dots span:first-child{background:var(--white)}
.hero-edge{position:absolute;left:0;bottom:0}

/* welcome */
.welcome{top:750px;left:0;width:1200px;height:508px}
.welcome-title{position:absolute;left:147px;top:45px;display:flex;gap:12px}
.welcome-title .brand-mark{width:50px;height:50px;margin-top:8px}
.welcome-title small{display:block;font-size:21px;color:var(--ink);font-weight:400}
.welcome-title strong{display:block;font-size:35px;color:var(--navy);font-weight:600;line-height:40px}
.welcome-text{position:absolute;left:147px;top:130px;width:390px;font-size:13px;line-height:24px}
.welcome-text p+p{margin-top:8px}
.welcome .btn{position:absolute;left:147px;top:379px;width:132px;height:39px;line-height:39px;text-align:center;font-size:13px}
.welcome-visual{position:absolute;left:568px;top:45px;width:490px;height:393px;background:linear-gradient(160deg,#3f64e0 0%,#1a2f85 50%,#1a1d2a 100%);clip-path:polygon(10% 60%,55% 25%,100% 58%,52% 100%)}

/* features */
.features{top:1258px;left:0;width:1200px;height:640px;background-color:var(--light);background-image:radial-gradient(#dfe2ee 1px,transparent 1px);background-size:8px 8px}
.feature{position:absolute;width:332px;text-align:center;color:var(--text)}
.feature h3{font-size:17px;font-weight:700;color:var(--ink);letter-spacing:.5px;text-transform:uppercase}
.feature p{font-size:14px;line-height:24px;margin-top:12px;padding:0 30px}
.feature svg{display:block;margin:0 auto 18px}
.feature.highlight{background:var(--blue);color:var(--white);top:93px;left:435px;height:336px;padding-top:30px;box-shadow:0 8px 20px rgba(11,26,75,.3)}
.feature.highlight h3,.feature.highlight p{color:var(--white)}
.features-edge{position:absolute;left:0;bottom:0}

/* philosophy */
.philosophy{top:1892px;left:0;width:1200px;height:520px}
.philosophy-visual{position:absolute;left:100px;top:50px;width:485px;height:393px;border-radius:46% 40% 44% 38%;background:linear-gradient(140deg,#dde4fb,#b9c6f2)}
.section-copy{position:absolute}
.section-copy h2{font-size:34px;line-height:42px;font-weight:600;color:var(--ink)}
.section-copy .lead{font-size:13px;line-height:22px;margin-top:20px}
.checks{list-style:none;margin-top:14px}
.checks li{position:relative;padding-left:26px;font-size:13px;line-height:21px;margin-bottom:8px}
.checks li::before{content:"";position:absolute;left:2px;top:5px;width:9px;height:9px;border:2px solid var(--blue);border-radius:50%}
.checks li::after{content:"";position:absolute;left:6px;top:9px;width:5px;height:5px;background:var(--blue);border-radius:50%}
.philosophy .section-copy{left:640px;top:56px;width:450px}
.wave{position:absolute;left:167px;top:2430px}

/* strategy */
.strategy{top:2496px;left:0;width:1200px;height:420px}
.strategy .section-copy{left:145px;top:20px;width:430px}
.rule{width:64px;height:3px;background:var(--blue);margin-top:26px}
.strategy-visual{position:absolute;left:624px;top:10px;width:443px;height:394px;background:linear-gradient(135deg,#eef1fb 0%,#d7def7 60%,#f4f5fb 100%);border-radius:6px}

/* approach */
.approach{top:2985px;left:0;width:1200px;height:640px;background:linear-gradient(180deg,#1b3aa5,#1a36a0);clip-path:polygon(0 0,100% 0,100% 560px,50% 640px,0 560px);color:var(--white);text-align:center}
.approach h2{margin-top:62px;font-size:36px;font-weight:600}
.approach .intro{margin:24px auto 0;width:640px;font-size:16px;line-height:27px;font-weight:500}
.approach-card{position:absolute;top:246px;height:286px;background:var(--white);text-align:left;padding:24px 25px 0 26px;color:var(--text)}
.approach-card .icon{width:98px;height:98px;border-radius:50%;display:flex;align-items:center;justify-content:center;margin-bottom:24px}
.approach-card .icon.solid{background:var(--blue)}
.approach-card .icon.ring{border:3px solid var(--blue)}
.approach-card h3{font-size:16px;line-height:24px;font-weight:600;color:var(--ink)}
.approach-card p{font-size:13px;line-height:22px;margin-top:10px}
.next{position:absolute;top:372px;width:40px;height:40px;border-radius:50%;background:var(--white);border:2px solid var(--blue);display:flex;align-items:center;justify-content:center;z-index:2}

/* press */
.press{top:3625px;left:0;width:1200px;height:840px;background-color:var(--light);background-image:radial-gradient(#dfe2ee 1px,transparent 1px);background-size:8px 8px}
.press h2{position:absolute;left:0;width:1200px;top:135px;text-align:center;font-size:36px;font-weight:600;color:var(--navy)}
.press-feature{position:absolute;left:145px;top:250px;width:427px;height:362px;background:linear-gradient(160deg,#b7c2d6,#6b7791);overflow:hidden}
.press-feature .caption{position:absolute;left:76px;top:194px;width:351px;height:168px;background:rgba(27,58,165,.92);color:var(--white);padding:18px 22px}
.press-feature h3{font-size:17px;line-height:25px;font-weight:600}
.meta{display:flex;gap:18px;align-items:center;font-size:12px;font-weight:600;margin-top:8px}
.meta span{display:flex;gap:6px;align-items:center}
.press-feature p{font-size:12px;line-height:20px;margin-top:10px}
.press-item{position:absolute;left:604px;width:451px;height:169px;background:var(--white);display:flex;box-shadow:0 2px 6px rgba(11,26,75,.08)}
.press-item .thumb{width:187px;height:169px;flex:none}
.press-item .body{padding:14px 18px 0 24px}
.press-item h3{font-size:16px;font-weight:500;color:var(--ink)}
.press-item .meta{color:var(--blue)}
.press-item p{font-size:12px;line-height:20px;margin-top:12px}

/* contact */
.contact{top:4440px;left:0;width:1200px;height:512px;background:linear-gradient(180deg,#0e1f70,#0b1a5a);clip-path:polygon(0 40px,50% 0,100% 40px,100% 100%,0 100%);color:var(--white)}
.contact h2{position:absolute;top:70px;font-size:30px;font-weight:600;letter-spacing:.5px}
.contact .bar{position:absolute;top:114px;width:60px;height:3px;background:var(--white)}
.field{position:absolute;height:38px;background:var(--white);font-size:12px;color:var(--text);padding:12px 16px}
.submit{position:absolute;left:143px;top:385px;width:163px;height:42px;line-height:42px;text-align:center;font-size:16px;box-shadow:none}
.contact-row{position:absolute;left:707px;display:flex;gap:22px}
.circle{width:44px;height:44px;border-radius:50%;background:var(--white);display:flex;align-items:center;justify-content:center;flex:none}
.contact-row .info{font-size:15px;line-height:26px;font-weight:600}
.socials{position:absolute;left:707px;top:383px;display:flex;gap:11px}
.socials span{width:36px;height:36px;border:2px solid var(--white);border-radius:50%}

/* footer */
.site-footer{top:4952px;left:0;width:1200px;height:234px;text-align:center}
.site-footer .brand{justify-content:center;margin-top:58px;font-size:38px}
.footer-nav{margin-top:30px;font-size:15px;color:var(--ink)}
.footer-nav span{margin:0 6px;color:var(--text)}
.copyright{margin-top:22px;font-size:15px;color:var(--ink)}
</style>
</head>
<body>

<header class="site-header abs">
  <a class="brand" href="#"><span class="brand-mark"></span>Valdmore Funds</a>
  <nav class="main-nav">
    <span class="active">Home</span><span>Philosophy</span><span>How to invest</span><span>What we do</span><span>Insights</span><span>Contact</span>
  </nav>
  <a class="btn login" href="#">Login</a>
</header>

<section class="hero abs">
  <div class="hero-visual" role="img" aria-label="Glowing blue 3D bar and line chart rising over a world map"></div>
  <div class="hero-copy">
    <h1>YOUR PERSONAL<br>INVESTMENT ADVISOR</h1>
    <p>Valdmore Funds is Your Global<br>Reference for Investment Advice</p>
    <a class="btn" href="#">Learn more</a>
    <div class="dots"><span></span><span></span><span></span></div>
  </div>
  <svg class="hero-edge" width="1200" height="110" viewBox="0 0 1200 110">
    <polygon points="0,70 600,20 1200,40 1200,110 0,110" fill="#1b3aa5"/>
    <polygon points="0,110 0,100 560,44 1200,80 1200,110" fill="#ffffff"/>
  </svg>
</section>

<section class="welcome abs">
  <div class="welcome-title">
    <span class="brand-mark"></span>
    <div><small>Welcome to</small><strong>Valdmore Funds</strong></div>
  </div>
  <div class="welcome-text">
    <p>We are a privately held firm dedicated to clients who have entrusted us with their wealth. We act solely and transparently in the best interest of our clients. We pride ourselves on our discretion and confidentiality.</p>
    <p>You can be assured of a totally Client-centric service, high quality, totally unbiased, investment advice. We are fee only based, i.e. we have no affiliations with any financial institutions – we do not take any commission from any investment product provider – We Work Only for You!</p>
  </div>
  <a class="btn" href="#">Learn more</a>
  <div class="welcome-visual" role="img" aria-label="Blue 3D bar chart standing on a tablet showing a line graph"></div>
</section>

<section class="features abs">
  <div class="feature" style="left:102px;top:108px">
    <svg width="96" height="90" viewBox="0 0 96 90" fill="none" stroke="#1b3aa5" stroke-width="3"><rect x="6" y="62" width="14" height="22"/><rect x="28" y="48" width="14" height="36"/><rect x="50" y="36" width="14" height="48"/><rect x="72" y="22" width="14" height="62"/><path d="M6 44 L36 22 L56 30 L88 6"/><path d="M78 6 H88 V16"/></svg>
    <h3>Why choose us?</h3>
    <p>We secure your interests by continuously keeping your Investment optimal natus accutium doloremque</p>
  </div>
  <div class="feature highlight">
    <svg width="106" height="100" viewBox="0 0 106 100" fill="none" stroke="#ffffff" stroke-width="3"><rect x="4" y="18" width="66" height="50" rx="3"/><path d="M28 68 L24 82 H52 L48 68"/><circle cx="26" cy="42" r="11"/><path d="M26 31 V42 H37"/><rect x="76" y="4" width="24" height="44" rx="3"/><rect x="48" y="54" width="54" height="36" rx="3"/><path d="M58 82 V72 M66 82 V66 M74 82 V70 M82 82 V62 M90 82 V74"/></svg>
    <h3>Investment Intelligence</h3>
    <p>Your Exclusive Access to European and American Markets and to Our Innovative Investment Approach. We attempt to design attractive long-term return portfolios, with low portfolio</p>
  </div>
  <div class="feature" style="left:765px;top:108px">
    <svg width="96" height="96" viewBox="0 0 96 96" fill="none" stroke="#1b3aa5" stroke-width="3"><circle cx="48" cy="14" r="8"/><path d="M34 38 a14 12 0 0 1 28 0 Z"/><circle cx="18" cy="56" r="8"/><path d="M4 82 a14 12 0 0 1 28 0 Z"/><circle cx="78" cy="56" r="8"/><path d="M64 82 a14 12 0 0 1 28 0 Z"/><path d="M24 30 L16 40 M72 30 L80 40 M38 70 H58 M52 64 L58 70 L52 76"/></svg>
    <h3>Client Focus</h3>
    <p>For Years Financial Institutions Have Said: “Client in the Center” but they have mainly offered standard solutions without much flexibility leaving the client</p>
  </div>
  <svg class="features-edge" width="1200" height="140" viewBox="0 0 1200 140">
    <polygon points="0,10 790,120 1200,10 1200,140 0,140" fill="#ffffff"/>
    <polyline points="200,40 790,122 1010,40" fill="none" stroke="#0b1a4b" stroke-width="7"/>
  </svg>
</section>

<section class="philosophy abs">
  <div class="philosophy-visual" role="img" aria-label="Illustration of a man standing beside a large tablet showing charts"></div>
  <div class="section-copy">
    <h2>Valdmore Investment Advisory Philosophy</h2>
    <p class="lead">Sed ut perspiciatis unde omnis iste natus error sit voluptatem accusantium doloremque laudantium, totam rem aperiam, eaque ipsa</p>
    <ul class="checks">
      <li>Systematic Adaption to Market Climate</li>
      <li>Attractive Risk Returns with Low Portfolio Turnover</li>
      <li>Europe and U.S. Investment Area</li>
      <li>Built to Follow or Outperform the Market During Upturns and Avoid Large Declines During Long – Term Market Turndowns</li>
      <li>Continuously Monitoring, Identifying and Implementing to Maintain Optimal Portfolio</li>
      <li>Long – Term Investment Strategy</li>
    </ul>
  </div>
</section>

<svg class="wave" width="866" height="20" viewBox="0 0 866 20"><path d="M0 10 Q108 2 216 10 T433 10 T650 10 T866 10" fill="none" stroke="#1b3aa5" stroke-width="2"/></svg>

<section class="strategy abs">
  <div class="section-copy">
    <h2>Valdmore Funds Investment Strategy</h2>
    <div class="rule"></div>
    <p class="lead">Our Main Objective is to Invest in Sustainable and Undervalued Mainly Large Cap Companies</p>
    <ul class="checks">
      <li>Excellent Historic Performance</li>
      <li>Value Invest</li>
      <li>Active Management</li>
      <li>Risk Control</li>
      <li>Low Portfolio Turnover</li>
      <li>Portfolio Management on clients own account</li>
    </ul>
  </div>
  <div class="strategy-visual" role="img" aria-label="Illustration of a team meeting around a table in front of a large dashboard of charts"></div>
</section>

<section class="approach abs">
  <h2>Our Approach</h2>
  <p class="intro">Valdmore Funds is truly different – We deliver Investment Services that sets us apart from our contemporaries</p>

  <article class="approach-card" style="left:145px;width:282px">
    <div class="icon solid"><svg width="52" height="52" viewBox="0 0 52 52" fill="none" stroke="#fff" stroke-width="3"><circle cx="26" cy="26" r="9"/><path d="M26 4 V12 M26 40 V48 M4 26 H12 M40 26 H48 M10 10 L16 16 M36 36 L42 42 M42 10 L36 16 M16 36 L10 42"/></svg></div>
    <h3>Valdmore Investment Management System VIMS®</h3>
    <p>Built on a combination of macroeconomic and fundamental analysis</p>
  </article>
  <div class="next" style="left:419px"><svg width="16" height="14" viewBox="0 0 16 14" fill="none" stroke="#1b3aa5" stroke-width="2"><path d="M2 2 L7 7 L2 12 M9 2 L14 7 L9 12"/></svg></div>

  <article class="approach-card" style="left:451px;width:290px">
    <div class="icon ring"><svg width="48" height="48" viewBox="0 0 48 48" fill="none" stroke="#1b3aa5" stroke-width="3"><rect x="6" y="4" width="36" height="40" rx="3"/><rect x="12" y="24" width="24" height="14"/><circle cx="24" cy="31" r="4"/><path d="M12 12 H22 M12 18 H30"/></svg></div>
    <h3>VIQS® Investment Generator</h3>
    <p>Valdmore iQ Software VIQS® is designed to analyse, forcast, generate and monitor an infinite number of personalized investment portfolios</p>
  </article>
  <div class="next" style="left:737px"><svg width="16" height="14" viewBox="0 0 16 14" fill="none" stroke="#1b3aa5" stroke-width="2"><path d="M2 2 L7 7 L2 12 M9 2 L14 7 L9 12"/></svg></div>

  <article class="approach-card" style="left:765px;width:292px">
    <div class="icon ring"><svg width="48" height="48" viewBox="0 0 48 48" fill="none" stroke="#1b3aa5" stroke-width="3"><rect x="8" y="4" width="32" height="40" rx="3"/><path d="M14 12 H34 M14 18 H34 M14 24 H28"/><rect x="16" y="30" width="16" height="8"/></svg></div>
    <h3>Services</h3>
    <p>VIMS® &amp; VIQS® enable Valdmore Funds to deliver customized services &amp; solutions to low cost &amp; risks with predictable returns</p>
  </article>
</section>

<section class="press abs">
  <h2>Press Releases</h2>
  <article class="press-feature" role="img" aria-label="Photo of smiling colleagues in an office">
    <div class="caption">
      <h3>Nemo enim ipsam voluptatem quia voluptas</h3>
      <div class="meta"><span>▦ Jan 25, 2019</span><span>|</span><span>◌ 2 comments</span></div>
      <p>Sed ut perspiciatis unde omnis iste natus error sit vuptatem accusantium doloremque</p>
    </div>
  </article>
  <article class="press-item" style="top:250px">
    <div class="thumb" role="img" aria-label="Photo of a family at a laptop" style="background:linear-gradient(150deg,#8ea7c8,#3e5f8c)"></div>
    <div class="body">
      <h3>Nemo enim ipsam volupta</h3>
      <div class="meta"><span>▦ Jan 25, 2019</span><span>◌ 2 comments</span></div>
      <p>Sed ut perspiciatis unde omnis iste natus error sit vuptatem aum doloremque</p>
    </div>
  </article>
  <article class="press-item" style="top:441px">
    <div class="thumb" role="img" aria-label="Photo of a city view overlaid with blue financial graphics" style="background:linear-gradient(150deg,#5f86c9,#1c2f70)"></div>
    <div class="body">
      <h3>Nemo enim ipsam volupta</h3>
      <div class="meta"><span>▦ Jan 25, 2019</span><span>◌ 2 comments</span></div>
      <p>Sed ut perspiciatis unde omnis iste natus error sit vuptatem aum doloremque</p>
    </div>
  </article>
</section>

<section class="contact abs">
  <h2 style="left:143px">GET IN TOUCH</h2>
  <div class="bar" style="left:143px"></div>
  <div class="field" style="left:143px;top:150px;width:252px">First Name</div>
  <div class="field" style="left:409px;top:150px;width:249px">Last Name</div>
  <div class="field" style="left:143px;top:204px;width:515px">Email Address</div>
  <div class="field" style="left:143px;top:258px;width:252px">City</div>
  <div class="field" style="left:409px;top:258px;width:249px">Phone Number</div>
  <div class="field" style="left:143px;top:311px;width:515px;height:52px">Message</div>
  <a class="btn submit" href="#">Submit now</a>

  <h2 style="left:707px">CONTACT US</h2>
  <div class="bar" style="left:707px"></div>
  <div class="contact-row" style="top:154px">
    <span class="circle"><svg width="18" height="22" viewBox="0 0 18 22"><path d="M9 1 a8 8 0 0 1 8 8 c0 6 -8 12 -8 12 s-8 -6 -8 -12 a8 8 0 0 1 8 -8z" fill="#1b3aa5"/><circle cx="9" cy="9" r="3" fill="#fff"/></svg></span>
    <div class="info">Address:<br>14 Rue des Tilleuls<br>L-2740 Luxembourg Luxembourg<br><span style="display:block;margin-top:10px">52, Harbour View Lane<br>SLM 2094 Sliema Malta</span></div>
  </div>
  <div class="contact-row" style="top:287px">
    <span class="circle"><svg width="20" height="20" viewBox="0 0 20 20"><path d="M4 1 L8 5 L6 8 C7 11 9 13 12 14 L15 12 L19 16 L16 19 C8 19 1 12 1 4 Z" fill="#1b3aa5"/></svg></span>
    <div class="info" style="font-size:18px;line-height:44px">Phone: +352 2690 4418</div>
  </div>
  <div class="socials" aria-label="Social media links"><span></span><span></span><span></span><span></span></div>
</section>

<footer class="site-footer abs">
  <a class="brand" href="#"><span class="brand-mark"></span>Valdmore Funds</a>
  <nav class="footer-nav">Home<span>|</span>Investment Intelligence<span>|</span>Thinking Beyond<span>|</span>What We Do<span>|</span>Login<span>|</span>Disclaimer<span>|</span>Contact Us</nav>
  <p class="copyright">Copyright 2019 Valdmore Funds. All rights reserved.</p>
</footer>

</body>
</html>
```